New business card/stationary for a consulting company

I am looking for a clean and very professional looking business card for my consulting company as well as corresponding stationary. I am uploading our logo. I like simple and powerful for the feel. No graphics but I am open on everything else. Below is my contact information but would like the final to be in a version I can add my employees information into and print. Thank you.

Daniel Whitcombe
dan@ferncliffadvisory.com
2870 North 9th Avenue, Summit Floor, Elm Ridge, Illinois 60531
www.ferncliffadvisory.com

Industry/Entity Type

Consulting

Contact Information for Business Card

Daniel Whitcombe
dan@ferncliffadvisory.com
www.ferncliffadvisory.com

Font styles to use
Serif
Sans Serif

Requirements
Must have
• Our logo and the business card details.
Nice to have
• our website www.ferncliffadvisory.com

```html
<!DOCTYPE html>
<html lang="en">
<head>
<meta charset="UTF-8">
<title>Ferncliff Advisory — Business Card</title>
<link href="https://fonts.googleapis.com/css2?family=Marcellus&family=Source+Sans+3:wght@400&family=Raleway:wght@300&display=swap" rel="stylesheet">
<style>
  :root {
    --backdrop: #e6e4e1;
    --card-white: #fbfbfc;
    --navy: #1c1f78;
    --ink: #2b2b33;
    --card-black: #111112;
    --silver: #c9c9cc;
    --silver-soft: #9a9a9e;
  }
  html, body {
    margin: 0;
    width: 1200px;
    height: 900px;
    overflow: hidden;
    background: var(--backdrop);
  }
  .canvas {
    width: 1200px;
    height: 900px;
    display: flex;
    align-items: center;
    justify-content: center;
    gap: 40px;
  }
  .card {
    width: 540px;
    height: 309px;
    box-sizing: border-box;
    position: relative;
    box-shadow: 0 6px 18px rgba(0,0,0,0.18);
  }

  /* Front */
  .card-front {
    background: var(--card-white);
    display: flex;
  }
  .brand-panel {
    width: 245px;
    display: flex;
    align-items: center;
    justify-content: center;
    gap: 10px;
  }
  .brand-square {
    width: 18px;
    height: 18px;
    background: var(--navy);
    flex: none;
  }
  .brand-name {
    font-family: "Marcellus", serif;
    font-size: 24px;
    color: var(--navy);
    line-height: 1.1;
  }
  .divider {
    width: 1px;
    background: var(--navy);
    margin: 42px 0 62px;
    opacity: 0.7;
  }
  .contact-panel {
    padding: 44px 0 0 24px;
    color: var(--ink);
    font-family: "Source Sans 3", sans-serif;
  }
  .person-name {
    font-family: "Marcellus", serif;
    font-size: 19px;
    letter-spacing: 0.04em;
    color: var(--navy);
    text-transform: uppercase;
    margin: 0 0 12px;
  }
  .address {
    font-size: 14.5px;
    line-height: 1.3;
    margin: 0 0 12px;
    font-style: normal;
  }
  .contact-line {
    display: flex;
    align-items: center;
    gap: 7px;
    font-size: 14.5px;
    line-height: 1.4;
  }
  .contact-line svg { flex: none; }

  /* Back */
  .card-back {
    background: var(--card-black);
    display: flex;
    align-items: center;
    justify-content: center;
    gap: 14px;
  }
  .back-square {
    width: 20px;
    height: 20px;
    background: var(--silver);
  }
  .back-name {
    font-family: "Marcellus", serif;
    font-size: 28px;
    letter-spacing: 0.08em;
    text-transform: uppercase;
    color: var(--silver);
  }
</style>
</head>
<body>
<main class="canvas">
  <section class="card card-front" aria-label="Business card front">
    <div class="brand-panel">
      <span class="brand-square"></span>
      <span class="brand-name">Ferncliff Advisory</span>
    </div>
    <div class="divider"></div>
    <div class="contact-panel">
      <h1 class="person-name">Daniel Whitcombe</h1>
      <address class="address">2870 North 9th Avenue,<br>Summit Floor, Elm Ridge,<br>Illinois 60531</address>
      <div class="contact-line">
        <svg width="12" height="9" viewBox="0 0 12 9" aria-hidden="true">
          <rect x="0.5" y="0.5" width="11" height="8" fill="var(--navy)"/>
          <path d="M0.5 0.8 L6 5 L11.5 0.8" stroke="#fff" stroke-width="1" fill="none"/>
        </svg>
        <span>dan@ferncliffadvisory.com</span>
      </div>
      <div class="contact-line">
        <svg width="11" height="11" viewBox="0 0 11 11" aria-hidden="true">
          <circle cx="5.5" cy="5.5" r="5.5" fill="var(--navy)"/>
          <path d="M0.5 5.5 H10.5 M5.5 0.5 C3 3 3 8 5.5 10.5 M5.5 0.5 C8 3 8 8 5.5 10.5" stroke="#fff" stroke-width="0.8" fill="none"/>
        </svg>
        <span>www.ferncliffadvisory.com</span>
      </div>
    </div>
  </section>

  <section class="card card-back" aria-label="Business card back">
    <span class="back-square"></span>
    <span class="back-name">Ferncliff Advisory</span>
  </section>
</main>
</body>
</html>
```